Ductless Mini Split Business Website

Copper Fern Services is looking to design an eye catching educational website about installing Ductless mini splits.

Similar to this company.
https://www.halvikstream.com/

Coding

Coded - Design and coding required

```html
<!DOCTYPE html>
<html lang="en">
<head>
<meta charset="utf-8">
<title>Ductless Heat Pumps FAQ – Copper Fern Services</title>
<link href="https://fonts.googleapis.com/css2?family=Mulish:wght@400;500;600&display=swap" rel="stylesheet">
<style>
:root{
  --ink:#1f1f1f;
  --heading:#262626;
  --muted:#9a9a9a;
  --footer-text:#5a5a5a;
  --accent:#fdd000;
  --accent-soft:#fffbcb;
  --line:#d9d9d9;
  --tint:#f6f9fd;
}
*{box-sizing:border-box;margin:0;padding:0}
html,body{width:1200px;height:2307px;overflow:hidden;background:#fff}
body{position:relative;font-family:"Mulish",sans-serif;color:var(--ink)}
.header-shape{position:absolute;left:0;top:0;width:1200px;height:240px;z-index:0}
.side-tint{position:absolute;right:-60px;top:985px;width:170px;height:200px;border-radius:50%;background:var(--tint);z-index:0}
.brand{position:absolute;left:38px;top:24px;display:flex;align-items:center;gap:10px;z-index:2}
.brand-dot{width:30px;height:30px;border-radius:50%;background:var(--accent)}
.brand-name{font-size:17px;font-weight:600;color:var(--ink)}
.main-nav{position:absolute;top:34px;right:46px;display:flex;gap:24px;z-index:2;font-size:15.5px;font-weight:500;color:#333}
.main-nav a{color:inherit;text-decoration:none;position:relative;display:flex;align-items:center;gap:4px}
.main-nav svg{width:9px;height:9px}
.main-nav .current::after{content:"";position:absolute;left:20px;right:20px;bottom:-9px;height:2px;background:var(--accent)}
.page-title{position:absolute;left:107px;top:164px;font-size:54px;font-weight:500;color:var(--heading);z-index:2;letter-spacing:-.3px}
.breadcrumb{position:absolute;left:107px;top:235px;font-size:15.5px;font-weight:500;color:#333;display:flex;align-items:center;gap:7px;z-index:2}
.breadcrumb svg{width:13px;height:13px}
.faq{position:absolute;left:107px;top:367px;width:988px;z-index:2}
.faq h2{font-size:29px;font-weight:500;color:var(--heading);line-height:36px;margin-bottom:12px}
.faq h3{font-size:21.5px;font-weight:500;color:var(--heading);line-height:30px;margin-bottom:12px}
.faq p{font-size:16px;line-height:32px;color:var(--muted);margin-bottom:26px;letter-spacing:-.1px}
.comment{position:absolute;left:107px;top:1574px;width:986px;z-index:2}
.comment h2{font-size:29px;font-weight:500;color:var(--heading);line-height:36px}
.field{position:absolute;border:1px solid var(--line);border-radius:24px;font-size:12.5px;color:#666;padding:0 18px;display:flex;align-items:center}
.field.name{left:0;top:59px;width:480px;height:44px}
.field.email{left:507px;top:59px;width:479px;height:44px}
.field.message{left:0;top:130px;width:986px;height:97px;align-items:flex-start;padding-top:20px}
.btn{position:absolute;left:1px;top:268px;width:150px;height:42px;border-radius:21px;background:var(--accent);color:#fff;font-size:14px;font-weight:600;display:flex;align-items:center;justify-content:center;box-shadow:0 8px 20px rgba(253,208,0,.25)}
.site-footer{position:absolute;left:0;top:1958px;width:1200px;height:349px;border-top:1px solid #f3f0e0}
.col{position:absolute;top:50px}
.col h4{font-size:21.5px;font-weight:500;color:var(--heading);line-height:30px;margin-bottom:13px}
.col ul{list-style:none}
.col li{font-size:14px;color:var(--footer-text);line-height:35px}
.col p{font-size:14px;color:var(--footer-text);line-height:29px}
.col-location{left:107px}
.col-company{left:360px}
.col-links{left:613px}
.col-about{left:783px;width:310px}
.phone{font-size:25px;color:var(--accent);margin-top:6px}
.socials{display:flex;gap:7px;margin-top:12px}
.socials span{width:36px;height:36px;border-radius:50%;display:block}
.s1{background:#3b5ba8}.s2{background:#d32323}.s3{background:var(--accent)}.s4{background:#e00}
.to-top{position:absolute;left:1111px;top:2218px;width:44px;height:44px;border-radius:50%;background:var(--accent);display:flex;align-items:center;justify-content:center;box-shadow:0 6px 18px rgba(253,208,0,.3)}
.copyright{position:absolute;left:93px;top:2262px;font-size:12px;color:#333}
</style>
</head>
<body>
<svg class="header-shape" viewBox="0 0 1200 240" aria-hidden="true">
  <path d="M250 0 H1200 V95 C1000 130 820 170 650 215 C600 228 560 232 540 225 C470 190 360 130 270 85 C235 65 232 20 250 0 Z" fill="var(--accent-soft)"/>
</svg>
<div class="side-tint"></div>

<header>
  <div class="brand"><span class="brand-dot"></span><span class="brand-name">Copper Fern Services</span></div>
  <nav class="main-nav">
    <a href="#">Home</a>
    <a href="#">About <svg viewBox="0 0 10 10"><path d="M1 3l4 4 4-4" fill="none" stroke="#555" stroke-width="1.2"/></svg></a>
    <a href="#">Ductless Heat Pumps <svg viewBox="0 0 10 10"><path d="M1 3l4 4 4-4" fill="none" stroke="#555" stroke-width="1.2"/></svg></a>
    <a href="#" class="current">Ductless Heat Pumps FAQ</a>
    <a href="#">Financing</a>
    <a href="#">Reviews</a>
    <a href="#">Contact</a>
  </nav>
</header>

<h1 class="page-title">Ductless Heat Pumps FAQ</h1>
<div class="breadcrumb">
  <svg viewBox="0 0 14 14"><path d="M7 1L1 6.5h2V13h3V9h2v4h3V6.5h2z" fill="#333"/></svg>
  <span>Home</span>
  <svg viewBox="0 0 10 10" style="width:8px;height:8px"><path d="M3 1l4 4-4 4" fill="none" stroke="#555" stroke-width="1.2"/></svg>
  <span>Ductless Heat Pumps FAQ</span>
</div>

<main>
<section class="faq">
  <h2>Copper Fern Ductless Heat Pumps FAQ</h2>
  <h3>What is a ductless heating and cooling system?</h3>
  <p>As the name connotes, ductless systems are highly efficient, zonal heating and cooling that requires no ductwork. Ductless systems consist of one or more indoor air handler units and an outdoor compressor unit linked by a refrigerant line. Each air handler creates a separate heating and cooling zone in various areas of a home and can be controlled independently.</p>
  <h3>What are the best applications for ductless systems?</h3>
  <p>One of the most popular applications of ductless systems is for homes without built-in air ducts. This is common in older homes that usually have baseboard heaters as their main source of heating. In fact, many of our customers are homeowners wanting to replace their baseboard heating with the safer and more energy-efficient ductless system.</p>
  <h3>How does a ductless system work and how is it controlled?</h3>
  <p>Ductless systems are basically heat pumps that offer both heating and cooling year-round. During the winter, ductless heat pumps work by pulling warm air from the outside and transferring it inside. In the summer, the system reverses directions and pull warm air from inside and transfer it outside to keep your home cool.</p>
  <h3>How much does a ductless system cost?</h3>
  <p>The average cost of a ductless system including the installation is around $4000, and that is for a single air handler only. Adding more air handlers and choosing models with greater heating capacities increases the price further. While the upfront cost may seem discouraging, highly efficient ductless systems can practically pay for themselves in savings. Additionally, Copper Fern Services offers flexible financing options to help you with this investment.</p>
  <h3>What kind of maintenance does a ductless system require?</h3>
  <p>Like other heating and cooling systems, ductless heat pumps require regular maintenance (once or twice a year or as stated in the manufacturer’s warranty) to ensure peak performance. Although basic maintenance such as keeping the coils and filters clean can easily be done by you, it is also crucial that you seek professional maintenance from Copper Fern Services to catch potential issues early and keep the manufacturer’s warranty intact.</p>
  <h3>How do I know what size of system my house needs?</h3>
  <p>Correct sizing is one of the most important factors to consider when purchasing heating and cooling systems, including ductless heat pumps. When the system is too small, it will fail to provide the total home comfort you deserve. Meanwhile, when it’s too large, the ductless system will only waste energy heating or cooling your home. Our Copper Fern ductless experts can carefully assess the requirements of your space or entire home and help you find the right size of ductless system.</p>
</section>

<section class="comment">
  <h2>Leave A Comment</h2>
  <div class="field name">Name</div>
  <div class="field email">Email</div>
  <div class="field message">Comment</div>
  <div class="btn">Post Comment</div>
</section>
</main>

<footer class="site-footer">
  <div class="col col-location">
    <h4>Location</h4>
    <p>2875 NE Larkspur Road,<br>Suite B12<br>Brambleton, OR 97340</p>
    <div class="phone">(500) 555-0148</div>
  </div>
  <div class="col col-company">
    <h4>Copper Fern Services</h4>
    <ul><li>Home</li><li>About</li><li>Ductless Heat Pumps</li><li>Ductless Heat Pumps FAQ</li></ul>
  </div>
  <div class="col col-links">
    <h4>Quick Link</h4>
    <ul><li>Financing</li><li>Contact Us</li><li>Privacy Policy</li><li>Sitemap</li></ul>
  </div>
  <div class="col col-about">
    <h4>About Us</h4>
    <p>Experience maximum comfort, better indoor air quality, and lower utility bills by installing ductless heat pumps in your home.</p>
    <div class="socials"><span class="s1"></span><span class="s2"></span><span class="s3"></span><span class="s4"></span></div>
  </div>
</footer>

<div class="to-top"><svg width="16" height="16" viewBox="0 0 16 16"><path d="M3 10l5-5 5 5" fill="none" stroke="#fff" stroke-width="2"/></svg></div>
<div class="copyright">Copyright ©2019 | All rights reserved</div>
</body>
</html>
```